Redesign of business card for Cedar Ridge Mechanical

We are looking for a new design for our business cards for Cedar Ridge Mechanical. We are a plumbing & HVAC construction company, operating on the West Coast of Canada and USA. Logo attached.
Industry/Entity Type
Construction - Plumbing & HVAC
Contact Information for Business Card
Name, address, phone numbers, email, website address
Look and feel
Each slider illustrates characteristics of the customer's brand and the style your logo design should communicate.

```html
<!DOCTYPE html>
<html lang="en">
<head>
<meta charset="utf-8">
<title>Cedar Ridge Mechanical — Business Card</title>
<link rel="stylesheet" href="https://fonts.googleapis.com/css2?family=Montserrat:wght@400;700&display=swap">
<style>
  :root {
    --backdrop: #1c1c1e;
    --card-white: #ffffff;
    --card-black: #0c0c0c;
    --ink: #111111;
    --ink-soft: #333333;
    --pattern-light: #3a3a3c;
    --pattern-dark: #0a0a0a;
  }
  * { margin: 0; padding: 0; box-sizing: border-box; }
  html, body {
    width: 1200px;
    height: 947px;
    overflow: hidden;
    background: var(--backdrop);
    font-family: "Montserrat", sans-serif;
  }
  .canvas { position: relative; width: 1200px; height: 947px; }
  .card {
    position: absolute;
    left: 240px;
    width: 720px;
    height: 411px;
    border-radius: 26px;
    overflow: hidden;
  }
  .card--back {
    top: 42px;
    background: var(--card-black);
    border: 3px solid #e8e8e8;
  }
  .back-pattern {
    position: absolute;
    inset: 0;
    background: linear-gradient(90deg, var(--pattern-light) 0%, #202022 45%, var(--pattern-dark) 100%);
  }
  .back-brand {
    position: absolute;
    right: 30px;
    bottom: 28px;
    display: flex;
    align-items: center;
    gap: 8px;
    color: #f2f2f2;
    font-weight: 700;
    font-size: 11px;
    letter-spacing: 0.06em;
    text-transform: uppercase;
  }
  .brand-square { width: 12px; height: 12px; border: 2px solid currentColor; }

  .card--front { top: 494px; background: var(--card-white); color: var(--ink); }
  .front-brand {
    position: absolute;
    left: 36px;
    top: 70px;
    display: flex;
    align-items: center;
    gap: 16px;
    font-weight: 700;
    font-size: 24px;
    line-height: 1.15;
    letter-spacing: 0.04em;
    text-transform: uppercase;
  }
  .front-brand .brand-square {
    width: 86px;
    height: 86px;
    border: 9px solid var(--ink);
    border-radius: 12px;
  }
  .person__name {
    position: absolute;
    right: 44px;
    top: 46px;
    font-weight: 700;
    font-size: 26px;
    letter-spacing: 0.04em;
    text-transform: uppercase;
  }
  .divider-row {
    position: absolute;
    left: 36px;
    right: 44px;
    top: 82px;
    display: flex;
    align-items: flex-end;
    gap: 6px;
  }
  .divider-row .rule {
    flex: 1;
    height: 1.5px;
    background: var(--ink);
    margin-bottom: 4px;
    margin-left: 360px;
  }
  .person__role { font-size: 15px; color: var(--ink-soft); }
  .divider-main {
    position: absolute;
    left: 36px;
    top: 214px;
    width: 420px;
    height: 1.5px;
    background: var(--ink);
  }
  .contact {
    position: absolute;
    right: 44px;
    top: 140px;
    list-style: none;
    font-size: 16px;
    color: var(--ink-soft);
  }
  .contact li {
    display: flex;
    justify-content: flex-end;
    align-items: center;
    gap: 12px;
    height: 30px;
  }
  .contact svg { width: 14px; height: 14px; fill: var(--ink); }
  .address {
    position: absolute;
    left: 36px;
    top: 300px;
    font-size: 16px;
    line-height: 1.5;
    color: var(--ink-soft);
  }
</style>
</head>
<body>
<main class="canvas">
  <section class="card card--back" aria-label="Card back">
    <div class="back-pattern" role="img" aria-label="Repeating tonal monogram pattern in glossy black on black"></div>
    <div class="back-brand"><span class="brand-square"></span>Cedar Ridge Mechanical</div>
  </section>

  <section class="card card--front" aria-label="Card front">
    <div class="front-brand">
      <span class="brand-square"></span>
      <span>Cedar Ridge<br>Mechanical</span>
    </div>

    <p class="person__name">Daniel Reyes</p>
    <div class="divider-row">
      <span class="rule"></span>
      <p class="person__role">Managing Director</p>
    </div>

    <ul class="contact">
      <li>123 456 789
        <svg viewBox="0 0 24 24" aria-hidden="true"><path d="M6.6 10.8a15.1 15.1 0 0 0 6.6 6.6l2.2-2.2a1 1 0 0 1 1-.25 11.4 11.4 0 0 0 3.6.57 1 1 0 0 1 1 1V20a1 1 0 0 1-1 1A17 17 0 0 1 3 4a1 1 0 0 1 1-1h3.5a1 1 0 0 1 1 1c0 1.25.2 2.45.57 3.57a1 1 0 0 1-.25 1z"/></svg>
      </li>
      <li>info@youremail.com
        <svg viewBox="0 0 24 24" aria-hidden="true"><path d="M2 5h20v14H2zm2 2v.5l8 5 8-5V7zm0 2.8V17h16V9.8l-8 5z"/></svg>
      </li>
      <li>www.yourwebsite.com
        <svg viewBox="0 0 24 24" aria-hidden="true"><circle cx="12" cy="12" r="10"/></svg>
      </li>
    </ul>

    <div class="divider-main"></div>
    <p class="address">Your address<br>City State, Zip 1234</p>
  </section>
</main>
</body>
</html>
```